Private Investigation Business Card Design

I need a business card for a new private investigation company named Brisk Inquiries. I perform mainly surveillance jobs, vehicle repossessions, document serves etc. The final design should aim for a professional look. The logo has a magnifying glass with stick man arms and legs and is in a running action to show the "Brisk" aspect of the name. If the colour scheme could remain the same as the website www.briskinquiries-demo.com.au with silvers,blacks and a couple electric blue highlights.
Industry/Entity Type
Business
Contact Information for Business Card
Morgan Kellaway
Brisk Inquiries
0487316204
PO Box 58, Carnwell NSW 2291
info@briskinquiries-demo.com.au
www.briskinquiries-demo.com.au
Look and feel

```html
<!DOCTYPE html>
<html lang="en">
<head>
<meta charset="utf-8">
<title>Brisk Inquiries – Business Card</title>
<link rel="stylesheet" href="https://fonts.googleapis.com/css2?family=Open+Sans:wght@400;600;700&display=swap">
<style>
  :root {
    --backdrop: #ecebea;
    --card-dark: #2a2929;
    --card-light: #ffffff;
    --ink-light: #f4f4f4;
    --ink-dark: #2b2b2b;
    --silver: #8d8f92;
    --silver-light: #e4e5e6;
    --electric-blue: #1e90ff;
    --rule: #333333;
  }
  * { box-sizing: border-box; margin: 0; padding: 0; }
  html, body { width: 1200px; height: 900px; overflow: hidden; }
  body {
    background: var(--backdrop);
    font-family: "Open Sans", Arial, sans-serif;
    position: relative;
  }
  .card {
    position: absolute;
    width: 556px;
    height: 343px;
    box-shadow: 0 6px 18px rgba(0,0,0,0.18);
    overflow: hidden;
  }

  /* Front card */
  .card-front {
    left: 238px; top: 62px;
    background: var(--card-dark);
    color: var(--ink-light);
  }
  .mascot-area {
    position: absolute;
    left: 0; top: 0;
    width: 250px; height: 100%;
    background:
      radial-gradient(circle at 42% 22%, #ffffff 0 34px, #d7d8da 35px 42px, transparent 43px),
      linear-gradient(100deg, #ffffff 0%, #f3f3f4 45%, #bfc1c3 78%, var(--card-dark) 100%);
  }
  .front-details {
    position: absolute;
    right: 34px; top: 40px;
    text-align: right;
  }
  .brand-name-front {
    font-weight: 700;
    font-size: 34px;
    line-height: 1;
    color: var(--ink-light);
    letter-spacing: 0.5px;
  }
  .brand-accent {
    display: block;
    margin: 10px 0 0 auto;
    width: 72px; height: 3px;
    background: var(--electric-blue);
  }
  .person-name {
    margin-top: 29px;
    font-weight: 600;
    font-size: 17px;
  }
  .person-company { font-size: 14px; margin-top: 2px; }
  .address { margin-top: 16px; font-size: 14px; line-height: 19px; }
  .contact-list { margin-top: 16px; list-style: none; font-size: 14px; }
  .contact-list li {
    display: flex; justify-content: flex-end; align-items: center;
    gap: 8px; line-height: 21px;
  }
  .contact-list svg { width: 11px; height: 11px; }

  /* Back card */
  .card-back {
    left: 457px; top: 518px;
    background: var(--card-light);
    color: var(--ink-dark);
  }
  .brand-lockup {
    position: absolute;
    left: 0; right: 0; top: 128px;
    display: flex; justify-content: center; align-items: center; gap: 16px;
  }
  .brand-name-back {
    font-weight: 700;
    font-size: 44px;
    color: var(--silver);
    letter-spacing: 0.5px;
  }
  .brand-dot {
    width: 34px; height: 34px; border-radius: 50%;
    background: var(--electric-blue);
  }
  .web-footer {
    position: absolute;
    left: 0; right: 0; top: 286px;
    display: flex; align-items: center; gap: 10px;
    font-size: 13px;
  }
  .web-footer .rule { flex: 1; height: 1px; background: var(--rule); }
</style>
</head>
<body>

<section class="card card-front">
  <div class="mascot-area" role="img" aria-label="Running magnifying-glass mascot illustration"></div>
  <div class="front-details">
    <div class="brand-name-front">Brisk Inquiries</div>
    <span class="brand-accent" aria-hidden="true"></span>
    <p class="person-name">Morgan Kellaway</p>
    <p class="person-company">Brisk Inquiries</p>
    <p class="address">PO Box 58, Carnwell<br>NSW 2291</p>
    <ul class="contact-list">
      <li>0487316204
        <svg viewBox="0 0 12 12" aria-hidden="true"><path fill="#1e90ff" d="M1 3c0-1 1-2 5-2s5 1 5 2v1H8V3H4v1H1z M2 5h8l1 5H1z"/></svg>
      </li>
      <li>info@briskinquiries-demo.com.au
        <svg viewBox="0 0 12 12" aria-hidden="true"><path fill="#1e90ff" d="M0 2h12v8H0z"/><path d="M1 3l5 4 5-4" fill="none" stroke="#2a2929" stroke-width="1"/></svg>
      </li>
      <li>www.briskinquiries-demo.com.au
        <svg viewBox="0 0 12 12" aria-hidden="true"><path d="M5 7l2-2M4 5L2 7a1.5 1.5 0 0 0 3 3l2-2M8 7l2-2a1.5 1.5 0 0 0-3-3L5 4" fill="none" stroke="#1e90ff" stroke-width="1.3"/></svg>
      </li>
    </ul>
  </div>
</section>

<section class="card card-back">
  <div class="brand-lockup">
    <span class="brand-name-back">Brisk Inquiries</span>
    <span class="brand-dot" aria-hidden="true"></span>
  </div>
  <div class="web-footer">
    <span class="rule"></span>
    <span>www.briskinquiries-demo.com.au</span>
    <span class="rule"></span>
  </div>
</section>

</body>
</html>
```